Infographic for a Christian church discipleship pathway

We need to take a fairly complex program that helps people in a Baptist church follow Jesus, and turn it into a simple graphic. This graphic does not have to explain the whole program, web pages and print materials will do that. But, it should be something that people see and understand what it is quickly. The attached graphic is only to give the key words and general direction of the program. It should not serve as a design guide. In other words, we want to see some other ideas how this information can be imparted graphically with concision and creativity. It's important to note, the categories at the top (pray daily, read daily, gather weekly) are first steps, starting points....one shouldn't move forward until they've incorporated these things into their life. However, the categories that follow (study, connect, serve, etc) are not necessarily steps to take in sequential order.

The diagrams we've provided are not what we expect. They are only to explain the program. Here is a verbal description: The motto of our church is "A Ready Church" (ready to serve, ready to love, ready for when Jesus returns). There are four words that describe a ready church member: FOCUSED on the return of Christ, FAITHFUL in a daily relationship with Jesus, PREPARED for any opportunity to be a supernatural vessel of God's worK, LOOKING to invite others into God's family. The first two are God's Work in Me (Focused and faithful); the second two are God's Work Through me (Prepared, looking). Please use those two things as you wish (Focused faithful prepared looking; and God's word in and through me). If they are clarifying, please use. If not, you don't have to use.

Additionally, the strategies we employ to be "a ready church" are 1. Prayer 2. God's Word, and 3. Biblical Community. (So, in other words, these three things help us be a people who is focused, faithful, prepared, and looking....which is a ready church.

To provide some information how we will build this out: this graphic will be used in print and digital content. The digital content will allow people to click on each category to access training and resources associated with that discipline. (Fasting, reflecting, etc).

www.kvt.church

Target Market(s)

35-50

Industry/Entity Type

Religious

Other font styles liked:
• Lato and/or Cambria

Requirements
Must have
• Fonts: lato, cambria. Colors#: 373E41, ebebe8, #a69677. Accent Colors: 80401D, #4e5730, #a5bac8
Nice to have
• A designer who has an understanding of what it means to incorporate the spiritual disciplines of the Christian faith into their life.

```html
<!DOCTYPE html>
<html lang="en">
<head>
<meta charset="utf-8">
<title>The Daily Path – Kingsvale Trinity Church</title>
<link rel="stylesheet" href="https://fonts.googleapis.com/css2?family=Lato:wght@300;400;700;900&display=swap">
<style>
  :root {
    --slate: #373E41;
    --paper: #ffffff;
    --mist: #ebebe8;
    --stone: #c6c6c6;
    --tan: #a69677;
    --rust-dark: #80401D;
    --rust: #a5532a;
    --olive-dark: #4e5730;
    --olive: #6b7a45;
    --backdrop: #666666;
  }
  * { box-sizing: border-box; margin: 0; padding: 0; }
  html, body {
    width: 1200px; height: 1200px; overflow: hidden;
    background: var(--backdrop);
    font-family: "Lato", sans-serif;
  }
  .sheet {
    position: absolute; left: 69px; top: 190px;
    width: 1328px; height: 1025px;
    background: var(--paper);
    transform: scale(0.8); transform-origin: top left;
  }
  .abs { position: absolute; }
  .top-band { left: 0; top: 0; }
  .bottom-band { left: 0; bottom: 0; width: 100%; height: 14px; background: var(--slate); }

  .brand { left: 118px; top: 104px; display: flex; align-items: center; gap: 18px; }
  .brand-mark { width: 22px; height: 22px; background: var(--slate); }
  .brand-name {
    font-weight: 900; color: var(--slate); font-size: 36px; line-height: 37px; letter-spacing: 1px;
  }

  .title {
    left: 481px; top: 70px; font-weight: 900; font-size: 100px; line-height: 1;
    color: var(--slate); letter-spacing: -1px; white-space: nowrap;
  }
  .subtitle {
    left: 483px; top: 174px; font-weight: 400; font-size: 38px; line-height: 1;
    color: var(--slate); white-space: nowrap;
  }

  .start { left: 58px; top: 266px; width: 267px; height: 150px; background: var(--tan); border-top-left-radius: 6px; }
  .start-arrow { position: absolute; left: 27px; top: 37px; }
  .start-label {
    position: absolute; left: 48px; top: 57px; color: #fff; font-weight: 700; font-size: 33px;
  }

  .stage { left: 58px; width: 267px; }
  .stage-words {
    position: absolute; left: 0; top: 0; width: 139px; height: 100%;
    display: flex; align-items: center; justify-content: center; gap: 8px;
  }
  .stage-words span {
    writing-mode: vertical-rl; transform: rotate(180deg);
    color: #fff; font-weight: 700; font-size: 44px; line-height: 1; letter-spacing: 0.5px;
  }
  .stage-note {
    position: absolute; left: 139px; top: 0; width: 128px; height: 100%;
    display: flex; align-items: center; justify-content: center;
  }
  .stage-note span {
    writing-mode: vertical-rl; transform: rotate(180deg);
    color: #fff; font-weight: 400; font-size: 21px; white-space: nowrap;
  }
  .stage-in { top: 416px; height: 269px; background: var(--rust); }
  .stage-in .stage-note { background: var(--rust-dark); }
  .stage-through { top: 685px; height: 278px; background: var(--olive); border-bottom-left-radius: 6px; }
  .stage-through .stage-note { background: var(--olive-dark); }

  .band { left: 325px; width: 943px; }
  .band-stone { background: var(--stone); }
  .band-mist { background: var(--mist); }
  .band-1 { top: 266px; height: 287px; border-top-right-radius: 10px; }
  .band-2 { top: 553px; height: 132px; }
  .band-3 { top: 685px; height: 163px; }
  .band-4 { top: 848px; height: 115px; border-bottom-right-radius: 10px; }

  .divider { top: 266px; width: 1.5px; height: 697px; background: var(--slate); }

  .practice-head { top: 266px; }
  .practice-bar {
    height: 44px; display: flex; align-items: center; justify-content: center;
    color: #fff; font-weight: 700; font-size: 25px;
  }
  .practice-desc {
    height: 93px; clip-path: polygon(0 0, 100% 0, 100% 66%, 50% 100%, 0 66%);
    color: #fff; font-size: 14px; line-height: 17px; text-align: center; padding-top: 18px;
  }
  .prayer .practice-bar, .community .practice-bar { background: var(--olive-dark); }
  .prayer .practice-desc, .community .practice-desc { background: var(--olive); }
  .word .practice-bar { background: var(--rust-dark); }
  .word .practice-desc { background: var(--rust); }
  .community .practice-bar { border-top-right-radius: 10px; }

  .first-step {
    width: 88px; height: 88px; border-radius: 50%; border: 3px solid #fff;
    display: flex; align-items: center; justify-content: center; text-align: center;
    color: #fff; font-weight: 700; font-size: 14.5px; line-height: 18px;
  }
  .step-olive { background: var(--olive-dark); }
  .step-rust { background: var(--rust-dark); }

  .discipline {
    width: 300px; text-align: center; font-weight: 700; font-size: 26px;
    color: var(--slate); line-height: 1;
  }
</style>
</head>
<body>
<main class="sheet">
  <svg class="abs top-band" width="1328" height="56" viewBox="0 0 1328 56" aria-hidden="true">
    <polygon points="0,0 1328,0 1328,56 504,56 480,25 0,25" fill="#373E41"/>
  </svg>

  <div class="abs brand">
    <div class="brand-mark"></div>
    <div class="brand-name">KINGSVALE<br>TRINITY<br>CHURCH</div>
  </div>

  <h1 class="abs title">THE DAILY PATH</h1>
  <p class="abs subtitle">RHYTHMS &amp; PRACTICES FOR A FAITHFUL LIFE</p>

  <div class="abs band band-stone band-1"></div>
  <div class="abs band band-mist band-2"></div>
  <div class="abs band band-stone band-3"></div>
  <div class="abs band band-mist band-4"></div>

  <svg class="abs" style="left:325px;top:553px" width="943" height="320" viewBox="0 0 943 320" aria-hidden="true">
    <g fill="#c6c6c6">
      <polygon points="145,0 205,0 175,25"/><polygon points="458,0 518,0 488,25"/><polygon points="770,0 830,0 800,25"/>
    </g>
    <g fill="#ebebe8">
      <polygon points="145,132 205,132 175,157"/><polygon points="458,132 518,132 488,157"/><polygon points="770,132 830,132 800,157"/>
    </g>
    <g fill="#c6c6c6">
      <polygon points="145,295 205,295 175,320"/><polygon points="458,295 518,295 488,320"/><polygon points="770,295 830,295 800,320"/>
    </g>
  </svg>

  <div class="abs divider" style="left:659px"></div>
  <div class="abs divider" style="left:968px"></div>

  <div class="abs start">
    <svg class="start-arrow" width="222" height="78" viewBox="0 0 222 78" aria-hidden="true">
      <polygon points="0,3 175,3 175,0 222,39 175,78 175,75 0,75" fill="#373E41"/>
    </svg>
    <span class="start-label">Start here</span>
  </div>

  <div class="abs stage stage-in">
    <div class="stage-words"><span>FOCUSED.</span><span>FAITHFUL.</span></div>
    <div class="stage-note"><span>God's Work In Me</span></div>
  </div>
  <div class="abs stage stage-through">
    <div class="stage-words"><span>PREPARED.</span><span>LOOKING.</span></div>
    <div class="stage-note"><span>God's Work Through Me</span></div>
  </div>
  <svg class="abs" style="left:325px;top:505px" width="36" height="80" viewBox="0 0 36 80" aria-hidden="true">
    <polygon points="0,0 36,40 0,80" fill="#80401D"/>
  </svg>
  <svg class="abs" style="left:325px;top:783px" width="37" height="80" viewBox="0 0 37 80" aria-hidden="true">
    <polygon points="0,0 37,40 0,80" fill="#4e5730"/>
  </svg>

  <div class="abs practice-head prayer" style="left:358px;width:294px">
    <div class="practice-bar">PRAYER</div>
    <div class="practice-desc">Become a person devoted to<br>prayer each day of your life.</div>
  </div>
  <div class="abs practice-head word" style="left:667px;width:294px">
    <div class="practice-bar">God's Word</div>
    <div class="practice-desc">Build a daily habit of beholding<br>God in His Word.</div>
  </div>
  <div class="abs practice-head community" style="left:977px;width:291px">
    <div class="practice-bar">Biblical Community</div>
    <div class="practice-desc">Engage deeply in<br>Christian community.</div>
  </div>

  <div class="abs first-step step-olive" style="left:455px;top:374px">PRAY<br>DAILY</div>
  <div class="abs first-step step-rust" style="left:768px;top:374px">READ<br>DAILY</div>
  <div class="abs first-step step-olive" style="left:1069px;top:374px">GATHER<br>WEEKLY</div>

  <div class="abs discipline" style="left:349px;top:493px">REST</div>
  <div class="abs discipline" style="left:662px;top:490px">STUDY</div>
  <div class="abs discipline" style="left:969px;top:490px">CONNECT</div>

  <div class="abs discipline" style="left:349px;top:631px">CONNECT</div>
  <div class="abs discipline" style="left:662px;top:631px">MEMORIZE</div>
  <div class="abs discipline" style="left:969px;top:631px">LEARN</div>

  <div class="abs discipline" style="left:349px;top:759px">FAST</div>
  <div class="abs discipline" style="left:662px;top:759px">TEACH</div>
  <div class="abs discipline" style="left:969px;top:759px">GIVE</div>

  <div class="abs discipline" style="left:349px;top:898px">INTERCEDE</div>
  <div class="abs discipline" style="left:662px;top:898px">PROCLAIM</div>
  <div class="abs discipline" style="left:969px;top:898px">SERVE</div>

  <div class="abs bottom-band"></div>
</main>
</body>
</html>
```